HVAC Technical Manual Covers for Duct Design, Load Calculation and Equipment Selection

I work for an HVAC trade association that publishes technical manuals. We have a series of books that need new covers since there have been many changes.

I'd like the books to have a similar style to each other (like the current Manual V and K, see below). Here is a listing of all our current manuals https://www.owpr-guild.org/standards/technical-manuals. We plan on updating more in the future, like F, , W and XT. So I'd like a design that we can continue on.

The 3 covers I need are
1. Manual Q Residential Load Calculation
https://www.owpr-guild.org/standards/technical-manuals/manual-q
2. Manual K® - Residential Duct Systems
https://www.owpr-guild.org/standards/technical-manuals/manual-k
3. Manual V® - Residential Equipment Selection
https://www.owpr-guild.org/standards/technical-manuals/manual-v

I included our logos and style guide as a resource. But I'm open to all images and colors. The audience is primarily engineers, software developers, code officials and HVAC technicians. These 3 manuals are aimed at residential (single-family homes/townhomes) in the United States.

The audience is primarily engineers, software developers, code officials and HVAC technicians.

HVACR, Air Conditioning

Sans Serif

• OWPR Logo, manual letter and full title. Single Family or townhome images
• commercial buildings, mini splits, hardhats

```html
<!DOCTYPE html>
<html lang="en">
<head>
<meta charset="utf-8">
<title>OWPR Technical Manual Covers</title>
<link href="https://fonts.googleapis.com/css2?family=Montserrat:wght@200;500;600;700&display=swap" rel="stylesheet">
<style>
  :root {
    --backdrop: #c8c8c8;
    --sky-light: #5fb4ec;
    --sky-mid: #2a86dc;
    --sky-deep: #0b4f9e;
    --sky-pale: #9fd4f2;
    --brick: #a8442e;
    --brick-dark: #6e2a1e;
    --foliage: #3d5a2a;
    --paint-yellow: #d8b650;
    --white: #ffffff;
    --ink: #1d1d1f;
  }
  * { box-sizing: border-box; margin: 0; padding: 0; }
  html, body {
    width: 1200px;
    height: 800px;
    overflow: hidden;
    background: var(--backdrop);
    font-family: "Montserrat", sans-serif;
  }
  .cover-row {
    position: absolute;
    inset: 0;
    display: flex;
    justify-content: center;
    align-items: center;
    gap: 40px;
  }
  .cover {
    position: relative;
    width: 330px;
    height: 427px;
    overflow: hidden;
    box-shadow: 0 18px 30px rgba(0, 0, 0, 0.22);
  }
  .cover-photo {
    position: absolute;
    inset: 0;
  }
  .cover--q .cover-photo {
    background:
      linear-gradient(160deg, transparent 52%, var(--brick) 53%, var(--brick-dark) 100%),
      linear-gradient(180deg, var(--sky-light) 0%, var(--sky-mid) 60%, var(--sky-mid) 100%);
  }
  .cover--v .cover-photo {
    background:
      linear-gradient(165deg, transparent 55%, var(--paint-yellow) 56%, var(--foliage) 100%),
      linear-gradient(180deg, var(--sky-deep) 0%, var(--sky-mid) 45%, #5aa4ea 100%);
  }
  .cover--k .cover-photo {
    background:
      linear-gradient(200deg, transparent 42%, var(--brick) 43%, var(--brick-dark) 80%, var(--foliage) 100%),
      linear-gradient(180deg, #5a8fdc 0%, var(--sky-pale) 70%, #c8ecf7 100%);
  }
  .manual-letter {
    position: absolute;
    top: 30px;
    left: 104px;
    width: 216px;
    text-align: center;
    font-weight: 600;
    font-size: 250px;
    line-height: 1;
    color: var(--white);
    letter-spacing: -4px;
  }
  .manual-word {
    position: absolute;
    top: 52px;
    left: 70px;
    transform-origin: left top;
    transform: rotate(90deg) translateY(-100%);
    font-weight: 200;
    font-size: 30px;
    letter-spacing: 9px;
    color: var(--white);
    white-space: nowrap;
  }
  .title-corner {
    position: absolute;
    right: 0;
    bottom: 0;
    width: 100%;
    height: 100%;
  }
  .manual-title {
    position: absolute;
    right: 20px;
    bottom: 36px;
    font-weight: 500;
    font-size: 12px;
    line-height: 16px;
    letter-spacing: 1px;
    color: var(--ink);
    text-align: right;
    text-transform: uppercase;
  }
  .publisher {
    position: absolute;
    left: 24px;
    bottom: 26px;
    display: flex;
    align-items: center;
    gap: 6px;
    font-weight: 600;
    font-size: 20px;
    color: var(--white);
  }
  .publisher-mark {
    width: 10px;
    height: 10px;
    background: var(--white);
  }
</style>
</head>
<body>
  <main class="cover-row">

    <article class="cover cover--q">
      <div class="cover-photo" role="img" aria-label="Row of brick and painted townhomes against a blue sky"></div>
      <span class="manual-letter">Q</span>
      <span class="manual-word">MANUAL</span>
      <svg class="title-corner" viewBox="0 0 330 427" preserveAspectRatio="none" aria-hidden="true">
        <polygon points="330,200 330,427 110,427" fill="var(--white)"/>
      </svg>
      <h1 class="manual-title">Residential<br>Load<br>Calculation</h1>
      <div class="publisher"><span class="publisher-mark"></span>OWPR</div>
    </article>

    <article class="cover cover--v">
      <div class="cover-photo" role="img" aria-label="Colourful Victorian single-family homes with gabled roofs under a deep blue sky"></div>
      <span class="manual-letter">V</span>
      <span class="manual-word">MANUAL</span>
      <svg class="title-corner" viewBox="0 0 330 427" preserveAspectRatio="none" aria-hidden="true">
        <polygon points="330,200 330,427 110,427" fill="var(--white)"/>
      </svg>
      <h1 class="manual-title">Residential<br>Equipment<br>Selection</h1>
      <div class="publisher"><span class="publisher-mark"></span>OWPR</div>
    </article>

    <article class="cover cover--k">
      <div class="cover-photo" role="img" aria-label="Red brick townhomes with green copper turrets and street trees under a pale sky"></div>
      <span class="manual-letter">K</span>
      <span class="manual-word">MANUAL</span>
      <svg class="title-corner" viewBox="0 0 330 427" preserveAspectRatio="none" aria-hidden="true">
        <polygon points="330,200 330,427 110,427" fill="var(--white)"/>
      </svg>
      <h1 class="manual-title">Residential<br>Duct<br>Systems</h1>
      <div class="publisher"><span class="publisher-mark"></span>OWPR</div>
    </article>

  </main>
</body>
</html>
```